New Business Card Design Project

We require a business card design for Vexalund, a newly established Indian company.
Our focus is on the development, manufacturing, and export of a diverse array of pharmaceutical products on a global scale. The card should convey a professional appearance, as our primary markets are in Africa, China, and Southeast Asian nations.
We envision a two-sided business card, with the reverse side dedicated to a logo set against a solid color or an elegantly designed pattern. The corners should be rounded. We would appreciate seeing both horizontal and vertical design options. We trust the designer to utilize their expertise in creating this design.

The content for the business card is included in the attached Word file.

Target Market(s)

Our primary markets are in Africa, China, and Southeast Asian, Latin America, Maldives, Sri Lanka

Industry/Entity Type

Pharmaceutical Manufacturing and Export

Contact Information for Business Card

Colors

Designer to choose colors to be used in the design.

Requirements
Must have
• The reverse side of the business card features solely the logo along with the tagline, "Remedies of Life."
Should not have
• The logo should not exceed two instances, encompassing both the front and back sides of the card.

```html
<!DOCTYPE html>
<html lang="en">
<head>
<meta charset="utf-8">
<title>Vexalund – Business Card</title>
<link rel="stylesheet" href="https://fonts.googleapis.com/css2?family=Open+Sans:wght@400;600;700&display=swap">
<style>
  :root {
    --backdrop: #d6ccbf;
    --card-clear: #e6ded3;
    --card-edge: #f4efe8;
    --card-dark: #1c1a1a;
    --teal: #1f88a4;
    --red: #c8412b;
    --ink-light: #d9c9b1;
  }
  * { box-sizing: border-box; margin: 0; padding: 0; }
  html, body {
    width: 1200px;
    height: 1046px;
    overflow: hidden;
    background: var(--backdrop);
    font-family: "Open Sans", Arial, sans-serif;
  }
  .business-card {
    position: absolute;
    left: 152px;
    top: 292px;
    width: 943px;
    height: 514px;
    border-radius: 32px;
    overflow: hidden;
    background: var(--card-clear);
    box-shadow: 0 0 0 2px var(--card-edge), 0 18px 40px rgba(0,0,0,.18);
  }
  .card-dark-field {
    position: absolute;
    inset: 0;
    width: 943px;
    height: 514px;
  }
  .card-dark-field path { fill: var(--card-dark); }
  .brand-mark {
    position: absolute;
    left: 760px;
    top: 62px;
    width: 48px;
    height: 48px;
    border-radius: 50%;
    background: var(--teal);
  }
  .brand-name {
    position: absolute;
    right: 31px;
    top: 150px;
    font-weight: 700;
    font-size: 50px;
    line-height: 1.1;
    color: var(--teal);
    letter-spacing: -0.5px;
  }
  .person-name {
    position: absolute;
    right: 33px;
    top: 240px;
    font-size: 35px;
    line-height: 1.1;
    color: var(--teal);
    white-space: nowrap;
  }
  .person-name .first { font-weight: 700; }
  .person-name .rest { font-weight: 400; }
  .person-role {
    position: absolute;
    right: 33px;
    top: 287px;
    font-size: 20px;
    line-height: 1.2;
    color: var(--ink-light);
  }
  .accent-bar {
    position: absolute;
    right: 0;
    top: 254px;
    width: 22px;
    height: 55px;
    background: var(--red);
  }
  .address {
    position: absolute;
    right: 33px;
    top: 332px;
    font-style: normal;
    font-size: 19px;
    line-height: 28px;
    text-align: right;
    color: var(--teal);
    letter-spacing: .3px;
  }
  .contact-list {
    position: absolute;
    right: 32px;
    top: 405px;
    list-style: none;
  }
  .contact-item {
    display: flex;
    justify-content: flex-end;
    align-items: center;
    gap: 16px;
    height: 27px;
    font-size: 19px;
    color: var(--ink-light);
    letter-spacing: .3px;
  }
  .contact-icon { width: 19px; height: 19px; flex: none; }
</style>
</head>
<body>
  <div class="business-card">
    <svg class="card-dark-field" viewBox="0 0 943 514" aria-hidden="true">
      <path d="M290 0 H943 V514 H560 Z"/>
    </svg>

    <span class="brand-mark" aria-hidden="true"></span>
    <h1 class="brand-name">Vexalund</h1>

    <p class="person-name"><span class="first">Arjun</span> <span class="rest">K. Malvade</span></p>
    <p class="person-role">CEO</p>
    <span class="accent-bar" aria-hidden="true"></span>

    <address class="address">
      12, Sunflower Lane,<br>
      Nashik, 422001, India
    </address>

    <ul class="contact-list">
      <li class="contact-item">
        <span>+919 400123456</span>
        <svg class="contact-icon" viewBox="0 0 20 20" aria-hidden="true">
          <rect x="5" y="1.5" width="10" height="17" rx="1.5" fill="none" stroke="var(--red)" stroke-width="2"/>
        </svg>
      </li>
      <li class="contact-item">
        <span>www.vexalund.com</span>
        <svg class="contact-icon" viewBox="0 0 20 20" aria-hidden="true">
          <circle cx="10" cy="10" r="8.5" fill="var(--teal)"/>
          <path d="M5 6 Q8 7 7 10 Q9 13 8 16 M12 4 Q11 8 14 9 Q16 11 15 14" fill="none" stroke="var(--card-dark)" stroke-width="1.4"/>
        </svg>
      </li>
      <li class="contact-item">
        <span>amalvade@vexalund.com</span>
        <svg class="contact-icon" viewBox="0 0 20 20" aria-hidden="true">
          <path d="M2 8 L10 2 L18 8 V18 H2 Z" fill="var(--red)"/>
          <path d="M2 8 L10 13 L18 8" fill="none" stroke="var(--card-dark)" stroke-width="1.2"/>
        </svg>
      </li>
    </ul>
  </div>
</body>
</html>
```